quickdeedsale.com redesign with wireframes, white space and custom form are very important

Need a new two column design that will convert easily to mobile responsive. Lots of white space. Winning design will probably be based on header area and making the custom form stand out. I want the header to be very much like www.tallgatevk.com except the form not to go up into the header.
Here are some of the websites I really like:
www.birchdwell.com
http://ourplotpurchasedirect.com/
http://kellbrightproperty.com/

We buy homes for cash and close fast. Our target is a home seller who is desperate to sell quickly.
I have uploaded my really ugly wireframe and my logo. I also uploaded my photo for the about us box and a possible photo to use for the header.
The copy on the wireframe is what I will be using except for the about us box.

Here is the exact link for video to frame in the top left box.
https://clipvault.example/Qm38pzrtLa

0592cd
85cae6
eaf1f7
fbee3d
ec1f27

• Everything on wireframe.
• Must use Verdana font and nothing should be smaller than 12 point. Most should be in 14 point. (except maybe inside of form)

```html
<!DOCTYPE html>
<html lang="en">
<head>
<meta charset="utf-8">
<title>quickdeedsale.com – Sell Your Home For Cash</title>
<link href="https://fonts.googleapis.com/css2?family=Montserrat:wght@400;500;600;700&family=Roboto:ital@1&display=swap" rel="stylesheet">
<style>
:root{
  --page-bg:#eceff2;
  --white:#ffffff;
  --accent:#f04e30;
  --blue:#1a56a6;
  --nav-blue:#1f5aa6;
  --ink:#222222;
  --body-text:#333333;
  --soft:#eaeef2;
  --frame:#e3e7ea;
  --form-border:#85c0e8;
  --line:#e2e4e6;
  --muted:#8a8f94;
}
*{box-sizing:border-box;margin:0;padding:0}
html,body{width:1200px;height:959px;overflow:hidden}
body{background:var(--page-bg);font-family:"Montserrat",Verdana,sans-serif;color:var(--body-text);position:relative}
.page{position:absolute;left:96px;top:0;width:996px;height:959px;background:var(--white);border-top:5px solid var(--accent)}
.abs{position:absolute}

/* header */
.brand{left:42px;top:40px;width:130px;font-weight:700;font-size:21px;line-height:24px;color:var(--accent);text-align:center}
.main-nav{left:210px;top:58px;display:flex;gap:28px}
.main-nav a{font-size:12.4px;font-weight:600;color:var(--nav-blue);text-decoration:none;white-space:nowrap}
.call-box{left:766px;top:38px;width:180px;text-align:center;color:var(--ink)}
.call-box .call-title{font-size:15px;font-weight:700}
.call-box .call-note{font-size:12px;font-weight:600}
.call-box .call-number{margin-top:2px;font-size:20px;font-weight:600;color:var(--accent);display:flex;align-items:center;justify-content:center;gap:6px}

/* hero */
.hero{left:32px;top:127px;width:923px;height:187px;background:var(--frame);padding:8px}
.hero-photo{width:100%;height:171px;background:linear-gradient(180deg,#3a8ad6 0%,#6aa6d8 35%,#9a8a6a 60%,#5a5040 100%);display:flex;flex-direction:column;align-items:center;justify-content:center;text-shadow:2px 2px 4px rgba(0,0,0,.55);color:var(--white)}
.hero-title{font-size:38px;font-weight:700;letter-spacing:-.3px;margin-top:-10px}
.hero-sub{font-size:29px;font-weight:700;margin-top:2px}
.hero-sub em{font-style:normal;color:var(--accent)}

/* side tabs */
.side-tabs{left:1092px;top:176px;width:33px;height:78px;background:var(--accent);border-radius:0 4px 4px 0;display:flex;flex-direction:column;align-items:center;justify-content:space-around;padding:4px 0}
.side-tabs .sep{width:100%;height:1px;background:rgba(255,255,255,.35)}

/* left column */
.benefits-title{left:47px;top:357px;font-size:18px;font-weight:600;color:var(--blue)}
.benefit-list{left:52px;top:389px;width:455px;list-style:none}
.benefit-list li{height:47px;display:flex;align-items:center;gap:10px;font-size:15px;border-bottom:1px solid var(--line);padding-left:14px}
.benefit-list li:last-child{border-bottom:none}
.video-intro{left:50px;top:554px;width:463px;height:59px;background:var(--soft);padding:8px 14px;font-size:16px;line-height:23px}
.video-frame{left:50px;top:636px;width:463px;height:267px;background:var(--frame);padding:8px}
.video-still{width:100%;height:251px;background:linear-gradient(180deg,#1f63c8 0%,#3a7fd8 45%,#d8d4c4 62%,#5a7a3a 80%,#4a6a2a 100%);position:relative}
.play-btn{position:absolute;left:184px;top:100px;width:79px;height:54px;background:var(--accent);border-radius:10px;display:flex;align-items:center;justify-content:center}
.section-rule{left:50px;top:925px;width:466px;height:4px;background:var(--frame)}
.cta-teaser{left:96px;top:945px;font-size:19px;font-weight:600;color:var(--accent);white-space:nowrap}

/* form */
.form-tab{left:591px;top:348px;width:343px;height:52px;background:var(--accent);border-radius:6px 6px 0 0;color:var(--white);display:flex;align-items:center;justify-content:center;gap:7px;font-size:17px;font-weight:600}
.form-tab em{font-size:19px;font-weight:700}
.form-tab .pointer{position:absolute;left:37px;bottom:-9px;width:0;height:0;border-left:7px solid transparent;border-right:7px solid transparent;border-top:9px solid var(--accent)}
.lead-form{left:591px;top:400px;width:343px;height:518px;background:var(--soft);border:6px solid var(--form-border);border-top:none;padding:0 13px}
.form-title{margin-top:18px;text-align:center;font-size:18px;font-weight:600;line-height:23px;color:var(--ink)}
.field{display:block;width:305px;height:34px;margin-top:11px;background:var(--white);border:1px solid #d5dadf;font-family:"Roboto",Verdana,sans-serif;font-style:italic;font-size:11.5px;color:var(--muted);padding:0 13px;line-height:32px;white-space:nowrap;overflow:hidden}
.field:first-of-type{margin-top:14px}
.submit-btn{margin-top:17px;width:307px;height:41px;background:var(--accent);border-radius:4px;display:flex;color:var(--white);font-weight:600;font-size:13.5px}
.submit-btn .label{flex:1;display:flex;align-items:center;padding-left:13px;white-space:nowrap}
.submit-btn .go{width:44px;border-left:1px solid rgba(255,255,255,.45);display:flex;align-items:center;justify-content:center;font-size:13px}
.form-foot{margin-top:17px;border-top:1px solid #d4d9dd;padding-top:12px;display:flex;justify-content:space-between;align-items:center}
.form-foot .privacy{font-size:9px;color:#666;padding-left:8px}
.share{display:flex;gap:6px}
.share span{width:20px;height:20px;border-radius:2px}
.share .s1{background:var(--accent)}
.share .s2{background:#3b5596}
.share .s3{background:#52a9e0}
.hours{left:582px;top:940px;width:363px;text-align:center;font-size:17px;color:var(--ink);white-space:nowrap}
.hours:before,.hours:after{content:"";position:absolute;top:10px;width:22px;height:10px;border-top:3px solid var(--frame)}
.hours:before{left:0;border-left:3px solid var(--frame)}
.hours:after{right:0;border-right:3px solid var(--frame)}
</style>
</head>
<body>
<div class="page">
  <header>
    <div class="abs brand">quickdeed<br>sale.com</div>
    <nav class="abs main-nav">
      <a href="#">Sell Your Home</a><a href="#">How it Works</a><a href="#">Stop Foreclosure</a><a href="#">Probate</a><a href="#">Contact</a>
    </nav>
    <div class="abs call-box">
      <div class="call-title">Call Us!</div>
      <div class="call-note">Nights and Weekends ok</div>
      <div class="call-number">
        <svg width="15" height="15" viewBox="0 0 16 16"><circle cx="8" cy="8" r="8" fill="#f04e30"/><path d="M5.2 4.2l1.3 1.3-.7 1.1c.6 1.3 1.5 2.2 2.8 2.8l1.1-.7 1.3 1.3-.9 1.2C7.6 11 5 8.4 4.2 5.1z" fill="#fff"/></svg>
        407-555-0186
      </div>
    </div>
  </header>

  <section class="abs hero">
    <div class="hero-photo" role="img" aria-label="Blurred photo of a single-storey house under blue sky">
      <div class="hero-title">Sell Your Home For Cash in 8 Days</div>
      <div class="hero-sub">We Buy Houses <em>Nationwide</em></div>
    </div>
  </section>

  <h2 class="abs benefits-title">These are the benefits of selling your home to us.</h2>
  <ul class="abs benefit-list">
    <li><svg width="21" height="21" viewBox="0 0 20 20"><circle cx="10" cy="10" r="10" fill="#f04e30"/><path d="M5.5 10.3l3 3 6-6.5" stroke="#fff" stroke-width="2.4" fill="none"/></svg>You pick the closing date</li>
    <li><svg width="21" height="21" viewBox="0 0 20 20"><circle cx="10" cy="10" r="10" fill="#f04e30"/><path d="M5.5 10.3l3 3 6-6.5" stroke="#fff" stroke-width="2.4" fill="none"/></svg>You pay NO commissions or fees</li>
    <li><svg width="21" height="21" viewBox="0 0 20 20"><circle cx="10" cy="10" r="10" fill="#f04e30"/><path d="M5.5 10.3l3 3 6-6.5" stroke="#fff" stroke-width="2.4" fill="none"/></svg>You don't have to paint, clean or make repairs</li>
  </ul>

  <p class="abs video-intro">Watch to see our president Marcus explain how easy it is to sell to us.</p>
  <div class="abs video-frame">
    <div class="video-still" role="img" aria-label="Video still of a white single-storey house with hedges and trees">
      <div class="play-btn"><svg width="22" height="24" viewBox="0 0 22 24"><path d="M2 1l19 11L2 23z" fill="#fff"/></svg></div>
    </div>
  </div>
  <div class="abs section-rule"></div>
  <p class="abs cta-teaser">Sell your home or house fast for cash to a</p>

  <div class="abs form-tab"><em>Yes!</em> I want to sell my home fast!<span class="pointer"></span></div>
  <form class="abs lead-form">
    <p class="form-title">Get a no obligation written offer<br>in 36 hours...</p>
    <span class="field">Your Name</span>
    <span class="field">Your phone number</span>
    <span class="field">Your Email Address</span>
    <span class="field">Property Address including City, State and Zip Code</span>
    <span class="field">Repairs needed if any</span>
    <span class="field">Asking price</span>
    <span class="field">Comments</span>
    <div class="submit-btn"><span class="label">Get started selling your home fast!</span><span class="go">&gt;&gt;</span></div>
    <div class="form-foot">
      <span class="privacy">Our Privacy Policy</span>
      <span class="share"><span class="s1"></span><span class="s2"></span><span class="s3"></span></span>
    </div>
  </form>
  <p class="abs hours">Call us 8am to 10 pm Eastern time.</p>
</div>

<aside class="abs side-tabs">
  <svg width="15" height="15" viewBox="0 0 16 16"><circle cx="8" cy="8" r="8" fill="#fff"/><path d="M5.2 4.2l1.3 1.3-.7 1.1c.6 1.3 1.5 2.2 2.8 2.8l1.1-.7 1.3 1.3-.9 1.2C7.6 11 5 8.4 4.2 5.1z" fill="#f04e30"/></svg>
  <span class="sep"></span>
  <svg width="15" height="12" viewBox="0 0 15 12"><rect width="15" height="12" rx="1.5" fill="#fff"/><path d="M1 1.5l6.5 5 6.5-5" stroke="#f04e30" stroke-width="1.4" fill="none"/></svg>
</aside>
</body>
</html>
```